Real Estate Company / Capital Needs Cards!

need business cards designed using the logos that were just designed by pixelbarn.

Reason: per designers request deadline extended 1 day…thank you.

Target Market(s)

Investors and clients looking to purchase real estate or invest in the business.

Industry/Entity Type

Business

Requirements
Must have
• two designs - one for the real estate logo and one for the capital logo, similar but slightly different.
Nice to have
• something to make it pop (perhaps on the back)
Should not have
• much color

```html
<!DOCTYPE html>
<html lang="en">
<head>
<meta charset="utf-8">
<title>Corvan Real Estate – Business Cards</title>
<link href="https://fonts.googleapis.com/css2?family=Open+Sans:wght@400;600&display=swap" rel="stylesheet">
<style>
  :root {
    --backdrop: #e9e6e2;
    --card-white: #ffffff;
    --panel-grey: #6d6e71;
    --divider-grey: #b9babc;
    --brand-grey: #7c7d80;
    --text-light: #ffffff;
    --text-dark: #3f4042;
  }
  * { box-sizing: border-box; margin: 0; padding: 0; }
  html, body {
    width: 1200px; height: 498px; overflow: hidden;
    background: var(--backdrop);
    font-family: "Open Sans", Arial, sans-serif;
  }
  .canvas { position: relative; width: 1200px; height: 498px; }
  .card {
    position: absolute; top: 84px;
    width: 540px; height: 330px;
    border-radius: 22px; overflow: hidden;
    background: var(--card-white);
    box-shadow: 0 6px 18px rgba(0,0,0,.18);
  }
  .card--front { left: 40px; }
  .card--back { left: 620px; }

  .brand { display: flex; align-items: center; gap: 12px; color: var(--brand-grey); font-weight: 400; }
  .brand__square { background: var(--brand-grey); flex: none; }
  .brand__text { display: flex; flex-direction: column; line-height: 1; }
  .brand__name { letter-spacing: .04em; }
  .brand__sub { letter-spacing: .12em; margin-top: 4px; }

  .front__brand { position: absolute; left: 36px; top: 142px; }
  .front__brand .brand__square { width: 34px; height: 46px; }
  .front__brand .brand__name { font-size: 30px; }
  .front__brand .brand__sub { font-size: 11px; }

  .front__divider {
    position: absolute; left: 245px; top: 0; bottom: 0;
    width: 8px; background: var(--divider-grey);
  }
  .front__panel {
    position: absolute; left: 253px; top: 0; right: 0; bottom: 0;
    background: var(--panel-grey); color: var(--text-light);
    padding: 68px 0 0 28px;
  }
  .contact__name { font-size: 18px; font-weight: 600; line-height: 1.2; }
  .contact__title { font-size: 15px; margin-top: 2px; }
  .contact__address { font-size: 13px; line-height: 1.5; margin-top: 24px; }
  .contact__list { list-style: none; margin-top: 26px; }
  .contact__item { display: flex; align-items: center; gap: 6px; font-size: 15px; line-height: 1.65; }
  .contact__item--email { font-size: 13px; }
  .contact__icon { width: 12px; height: 12px; fill: var(--text-light); flex: none; }

  .back__brand { position: absolute; left: 70px; top: 104px; gap: 20px; }
  .back__brand .brand__square { width: 62px; height: 96px; }
  .back__brand .brand__name { font-size: 56px; }
  .back__brand .brand__sub { font-size: 21px; margin-top: 6px; }
  .back__web {
    position: absolute; left: 0; right: 0; top: 258px; text-align: center;
    font-size: 15px; letter-spacing: .22em; color: var(--text-dark);
  }
  .back__web strong { font-weight: 600; }
</style>
</head>
<body>
<main class="canvas">
  <section class="card card--front" aria-label="Card front">
    <div class="brand front__brand">
      <span class="brand__square"></span>
      <span class="brand__text">
        <span class="brand__name">CORVAN</span>
        <span class="brand__sub">REAL ESTATE</span>
      </span>
    </div>
    <div class="front__divider"></div>
    <div class="front__panel">
      <p class="contact__name">Your Name</p>
      <p class="contact__title">Title</p>
      <p class="contact__address">Street Name, City Name<br>State ZipCode</p>
      <ul class="contact__list">
        <li class="contact__item">
          <svg class="contact__icon" viewBox="0 0 12 12"><path d="M2.5 0.5l2 2.5-1.2 1.4c.7 1.6 2 2.9 3.6 3.6l1.4-1.2 2.5 2-1.3 2.2C4.8 10.8 1.2 7.2.3 1.8z"/></svg>
          123-456-7980
        </li>
        <li class="contact__item">
          <svg class="contact__icon" viewBox="0 0 12 12"><rect x="3" y="1" width="6" height="4"/><rect x="1" y="5" width="10" height="6" rx="1"/></svg>
          123-568-7896
        </li>
        <li class="contact__item contact__item--email">
          <svg class="contact__icon" viewBox="0 0 12 12"><path d="M1 4l5-3 5 3v7H1z"/><path d="M1 4l5 3.5L11 4" fill="none" stroke="#6d6e71" stroke-width="1"/></svg>
          hello@corvanrealestate.com
        </li>
      </ul>
    </div>
  </section>

  <section class="card card--back" aria-label="Card back">
    <div class="brand back__brand">
      <span class="brand__square"></span>
      <span class="brand__text">
        <span class="brand__name">CORVAN</span>
        <span class="brand__sub">REAL ESTATE</span>
      </span>
    </div>
    <p class="back__web">www.<strong>corvanrealestate</strong>.com</p>
  </section>
</main>
</body>
</html>
```